Need a business card design for a residential architect.

You can get a sense of his work at www.tberlove.com

Would like a consistent look and feel between business card and website
.

Target Market(s)

Residential homeowners builders

Industry/Entity Type

Residential

Contact Information for Business Card

Dale Morrick
Principle
Morrick Architecture
418 Kestrel Lane
Menlo Park, CA 94025

dale@tberlove.com

tberlove.com
phone: 650-555-2716
Fax: 650-555-8043

Font styles to use
Sans Serif

Requirements
Must have
• Details above
Nice to have
• Would like a consistent look and feel between business card and website
Should not have
• None

```html
<!DOCTYPE html>
<html lang="en">
<head>
<meta charset="utf-8">
<title>Morrick Architecture — Business Card</title>
<link rel="stylesheet" href="https://fonts.googleapis.com/css2?family=Arimo:wght@400&display=swap">
<style>
  :root {
    --backdrop: #2b2a2a;
    --card-white: #ffffff;
    --card-mist: #dfe5ee;
    --ink: #4a4a4a;
    --ink-soft: #6b6b6b;
    --icon: #5a5a5a;
    --rule: #c9c9c9;
    --photo-warm: #d9a862;
    --photo-stone: #cdbba6;
    --photo-green: #6f7f3e;
    --photo-sky: #e6ecf2;
  }
  * { box-sizing: border-box; margin: 0; padding: 0; }
  html, body { width: 1200px; height: 900px; overflow: hidden; }
  body {
    background: var(--backdrop);
    font-family: "Arimo", Arial, sans-serif;
    color: var(--ink);
    display: flex;
    flex-direction: column;
    align-items: center;
    justify-content: center;
    gap: 40px;
  }
  .card {
    width: 630px;
    height: 360px;
    position: relative;
    overflow: hidden;
    box-shadow: 0 10px 24px rgba(0,0,0,.45);
  }
  /* Front */
  .card-front { background: var(--card-white); }
  .wordmark {
    position: absolute;
    left: 0; right: 0;
    top: 46px;
    text-align: center;
    color: var(--ink);
    font-size: 22px;
    letter-spacing: 5px;
    text-transform: uppercase;
    line-height: 1.3;
  }
  .wordmark-rule {
    position: absolute;
    top: 92px;
    left: 170px;
    width: 290px;
    height: 1px;
    background: linear-gradient(90deg, transparent, var(--rule) 30%, var(--rule) 70%, transparent);
  }
  .holder {
    position: absolute;
    right: 70px;
    top: 136px;
    text-align: right;
  }
  .holder-name { font-size: 19px; color: var(--ink); }
  .holder-title { font-size: 11px; color: var(--ink-soft); margin-top: 3px; }
  .contact-list {
    position: absolute;
    left: 56px;
    bottom: 40px;
    list-style: none;
  }
  .contact-item {
    display: flex;
    align-items: center;
    gap: 14px;
    font-size: 13px;
    color: var(--ink);
    height: 24px;
  }
  .contact-icon { width: 14px; height: 14px; fill: var(--icon); flex: none; }
  /* Back */
  .card-back { background: var(--card-mist); display: flex; }
  .back-brand {
    width: 36%;
    display: flex;
    align-items: center;
    justify-content: center;
  }
  .back-brand .wordmark-back {
    font-size: 16px;
    letter-spacing: 3px;
    text-transform: uppercase;
    text-align: center;
    line-height: 1.4;
    color: var(--ink);
  }
  .back-photo {
    flex: 1;
    background:
      linear-gradient(180deg, var(--photo-sky) 0%, transparent 22%),
      radial-gradient(ellipse at 40% 40%, var(--photo-warm) 0%, transparent 45%),
      linear-gradient(160deg, var(--photo-green) 0%, #8b7a52 35%, var(--photo-stone) 70%, #bfae98 100%);
  }
</style>
</head>
<body>
  <section class="card card-front" aria-label="Business card front">
    <div class="wordmark">Morrick<br>Architecture</div>
    <div class="wordmark-rule"></div>

    <div class="holder">
      <p class="holder-name">Dale Morrick</p>
      <p class="holder-title">Principle</p>
    </div>

    <ul class="contact-list">
      <li class="contact-item">
        <svg class="contact-icon" viewBox="0 0 16 16" aria-hidden="true"><path d="M8 1a5 5 0 0 0-5 5c0 3.6 5 9 5 9s5-5.4 5-9a5 5 0 0 0-5-5zm0 7a2 2 0 1 1 0-4 2 2 0 0 1 0 4z"/></svg>
        418 Kestrel Lane Menlo Park, CA 94025
      </li>
      <li class="contact-item">
        <svg class="contact-icon" viewBox="0 0 16 16" aria-hidden="true"><path d="M1 3h14v10H1z" fill="none" stroke="#5a5a5a" stroke-width="1.4"/><path d="M1 3l7 6 7-6" fill="none" stroke="#5a5a5a" stroke-width="1.4"/></svg>
        dale@tberlove.com
      </li>
      <li class="contact-item">
        <svg class="contact-icon" viewBox="0 0 16 16" aria-hidden="true"><g fill="none" stroke="#5a5a5a" stroke-width="1.2"><circle cx="8" cy="8" r="6.5"/><ellipse cx="8" cy="8" rx="3" ry="6.5"/><path d="M1.5 8h13M2.5 4.8h11M2.5 11.2h11"/></g></svg>
        tberlove.com
      </li>
      <li class="contact-item">
        <svg class="contact-icon" viewBox="0 0 16 16" aria-hidden="true"><path d="M4 1l2.5 3-1.5 2c.8 1.8 2.2 3.2 4 4l2-1.5 3 2.5-1.5 2.5C7 14 2 9 1.5 2.5z"/></svg>
        650-555-2716
      </li>
      <li class="contact-item">
        <svg class="contact-icon" viewBox="0 0 16 16" aria-hidden="true"><path d="M4 1h6l2 2v3H4z M2 7h12v6h-2v2H4v-2H2z"/></svg>
        650-555-8043
      </li>
    </ul>
  </section>

  <section class="card card-back" aria-label="Business card back">
    <div class="back-brand">
      <div class="wordmark-back">Morrick<br>Architecture</div>
    </div>
    <div class="back-photo" role="img" aria-label="Photograph of a residential patio at dusk with lit windows, stone paving, wicker chairs and a pool"></div>
  </section>
</body>
</html>
```